Can you make a cool and versatile Tarn Meridian Powerpoint template?
See www.tarnmeridian-example.co.uk and http://www.examplenet.invalid/company/tarn-meridian-ltd/ (on the right) to see how the logos are currently used - with interchangeably white and black backgrounds.
Target Market(s)
Marketing managers, product managers in HR technology, HR consultants
Industry/Entity Type
It Company
Font styles to use
Sans Serif
Requirements
Must have
- Master slide design, fonts, color theme, etc. Ideally two variations - one with white background (using colorful logo), one with a darker background (using black/white logo).

```html
<!DOCTYPE html>
<html lang="en">
<head>
<meta charset="utf-8">
<title>Market strategy for HCM vendors – Tarn Meridian</title>
<link rel="stylesheet" href="https://fonts.googleapis.com/css2?family=Fira+Sans+Extra+Condensed:wght@400&family=Source+Sans+3:wght@400;600&display=swap">
<style>
  :root {
    --canvas: #ffffff;
    --panel-grey: #e3e3e4;
    --panel-light: #f6f6f6;
    --card: #ffffff;
    --title-red: #e8432b;
    --text: #3e3e40;
    --rule: #d9d9d9;
    --green-light: #b9dc2a;
    --green-dark: #6aa516;
    --blue-light: #3a72c8;
    --blue-dark: #1c2a80;
    --warm-light: #f2a23a;
    --warm-dark: #7a4a1c;
    --brand-text: #3a3a3c;
    --brand-dot: #e8432b;
  }
  * { box-sizing: border-box; margin: 0; padding: 0; }
  html, body {
    width: 1200px; height: 1000px; overflow: hidden;
    background: var(--canvas);
  }
  .slide {
    position: relative; width: 1200px; height: 1000px;
    font-family: "Source Sans 3", "Myriad Pro", Arial, sans-serif;
    color: var(--text);
  }
  .backdrop {
    position: absolute; left: 28px; top: 85px; width: 1137px; height: 863px;
    background: radial-gradient(ellipse at 78% 55%, var(--panel-light) 0%, var(--panel-grey) 70%);
  }
  .slide-title {
    position: absolute; left: 73px; top: 118px;
    font-family: "Fira Sans Extra Condensed", "Myriad Pro Condensed", sans-serif;
    font-weight: 400; font-size: 74px; line-height: 1;
    color: var(--title-red); white-space: nowrap;
  }
  .pillar-card {
    position: absolute; left: 28px; top: 255px; width: 552px; height: 693px;
    background: var(--card);
    border-top-right-radius: 70px;
  }
  .pillar-art {
    position: absolute; border-radius: 6px;
  }
  .pillar-art--dev { left: 122px; top: 302px; width: 102px; height: 126px;
    background: linear-gradient(180deg, var(--green-light), var(--green-dark)); }
  .pillar-art--mkt { left: 122px; top: 462px; width: 102px; height: 126px;
    background: linear-gradient(180deg, var(--blue-light), var(--blue-dark)); }
  .pillar-art--win { left: 68px; top: 618px; width: 210px; height: 300px;
    background: linear-gradient(180deg, var(--warm-light), var(--warm-dark)); }
  .pillar-label {
    position: absolute; left: 270px; width: 270px;
    text-align: center; font-size: 38px; line-height: 38px; letter-spacing: 0.4px;
  }
  .pillar-label--dev { top: 324px; }
  .pillar-label--mkt { top: 478px; }
  .pillar-label--win { top: 632px; }
  .pillar-rule {
    position: absolute; left: 270px; width: 275px; height: 1px; background: var(--rule);
  }
  .pillar-rule--1 { top: 443px; }
  .pillar-rule--2 { top: 597px; }

  .wins {
    position: absolute; left: 645px; top: 271px; width: 520px;
    list-style: none;
  }
  .wins-lead {
    position: relative; font-size: 35px; line-height: 46px; letter-spacing: 0.3px;
  }
  .wins-lead::before {
    content: ""; position: absolute; left: -38px; top: 18px;
    width: 9px; height: 9px; border-radius: 50%; background: var(--title-red);
  }
  .wins-items { list-style: none; margin-top: 23px; margin-left: 41px; }
  .wins-items li {
    position: relative; font-size: 33px; line-height: 42.5px;
    letter-spacing: 0.5px; margin-bottom: 22px; white-space: nowrap;
  }
  .wins-items li::before {
    content: "–"; position: absolute; left: -41px; top: 0; color: var(--text);
  }
  .brand-tag {
    position: absolute; left: 975px; top: 880px; width: 190px; height: 68px;
    background: var(--card);
    display: flex; flex-direction: column; align-items: center; justify-content: center; gap: 6px;
  }
  .brand-tag__dot { width: 16px; height: 16px; border-radius: 50%; background: var(--brand-dot); }
  .brand-tag__name {
    font-weight: 600; font-size: 15.5px; letter-spacing: 0.3px;
    color: var(--brand-text); text-transform: uppercase;
  }
</style>
</head>
<body>
  <div class="slide">
    <div class="backdrop"></div>
    <h1 class="slide-title">Market strategy for HCM vendors</h1>

    <div class="pillar-card"></div>
    <div class="pillar-art pillar-art--dev" role="img" aria-label="Illustration: green droplet representing development resources"></div>
    <p class="pillar-label pillar-label--dev">Development<br>resources</p>
    <div class="pillar-rule pillar-rule--1"></div>
    <div class="pillar-art pillar-art--mkt" role="img" aria-label="Illustration: blue droplet representing marketing budgets"></div>
    <p class="pillar-label pillar-label--mkt">Marketing<br>budgets</p>
    <div class="pillar-rule pillar-rule--2"></div>
    <div class="pillar-art pillar-art--win" role="img" aria-label="Illustration: orange droplet landing in a brown cup, representing increased win rates"></div>
    <p class="pillar-label pillar-label--win">Increased<br>win rates</p>

    <ul class="wins">
      <li>
        <p class="wins-lead">Quick wins for Tarn Meridian<br>customers include:</p>
        <ul class="wins-items">
          <li>Development resources spent<br>developing unique<br>capabilities customers are<br>willing to pay for</li>
          <li>Marketing budgets spent<br>where the buyers are</li>
          <li>Increased win rates and<br>shorter sales cycles through<br>ROI selling</li>
        </ul>
      </li>
    </ul>

    <div class="brand-tag">
      <span class="brand-tag__dot"></span>
      <span class="brand-tag__name">Tarn Meridian</span>
    </div>
  </div>
</body>
</html>
```